Stationery Design Project for Nimbora, Chicago

Nimbora, a street parking application which helps car drivers find a street parking spot by offering an ideal path along which to look for parking. This path is calculated by our algorithm based on data (e.g. historical data, baseball games schedule, etc.). Along this path the driver will find a spot and will also save 70% of the search time. Customer we target is reg. between 21 and 45 yo.

We envision something young, fresh, bright and original. Slightly abstract maybe. It should represent the idea and elements of finding street parking in the city, e.g. car(s), parking spot, people, city, etc. (just ideas!).

Logo is attached.

Requirement:
- Business Cards (2 Sided Full Color CMYK)
- Letterhead (1 Sided Full Color CMYK)
- Envelope (1 Sided Full Color CMYK)
- Sticker (1 Sided Full Color CMYK), round with a 2inch diameter.

Reason: We're starting to get more and more designs and need more time to look into all of them. Very exciting!! Thanks to everybody!

Hi all, we're in the process of selecting our favs. Though choices!!! Really good submissions. Will keep you posted and sorry for the delay.

Target Market(s)

Car drivers and owners between 21 and 45

Industry/Entity Type

Parking

Requirements
Must have
• Sticker should be round and include company URL nimbora.com and the new logo which we will attach soon.
Should not have
• Should not be too serious or boring.

```html
<!DOCTYPE html>
<html lang="en">
<head>
<meta charset="utf-8">
<title>Nimbora Business Card</title>
<link href="https://fonts.googleapis.com/css2?family=Source+Sans+3:wght@400;600;700&display=swap" rel="stylesheet">
<style>
  :root {
    --backdrop: #e6e7e8;
    --card-white: #ffffff;
    --card-grey: #58595b;
    --card-black: #050505;
    --band-dark: #3a3b3d;
    --band-dark-edge: #141414;
    --brand-blue: #1a74c4;
    --brand-blue-deep: #1c3f9e;
    --ink-dark: #2b2b2b;
    --ink-grey: #58595b;
    --ink-light: #ffffff;
  }
  * { margin: 0; padding: 0; box-sizing: border-box; }
  html, body { width: 1200px; height: 954px; overflow: hidden; }
  body {
    background: var(--backdrop);
    font-family: "Source Sans 3", "Myriad Pro", Arial, sans-serif;
    position: relative;
  }
  .card {
    position: absolute;
    top: 77px;
    width: 454px;
    height: 795px;
    border-radius: 28px;
    overflow: hidden;
  }
  .card--front { left: 79px; background: var(--card-white); }
  .card--back {
    left: 633px;
    background:
      radial-gradient(ellipse 70% 55% at 38% 52%, var(--card-black) 45%, #2a2a2b 80%, var(--card-grey) 100%);
  }
  .card--back .card__top { position: absolute; left: 0; top: 0; width: 100%; height: 70px; background: var(--card-grey); }
  .card__band { position: absolute; left: 0; top: 70px; width: 454px; height: 183px; display: block; }
  .card__road {
    position: absolute; right: 0; bottom: 0; width: 210px; height: 380px; display: block;
  }
  .brand-name {
    position: absolute; left: 40px; top: 262px;
    font-size: 100px; font-weight: 600; line-height: 1; letter-spacing: 1px;
  }
  .card--front .brand-name { color: var(--ink-dark); }
  .card--back .brand-name { color: var(--ink-light); }
  .person { position: absolute; left: 39px; top: 410px; color: var(--ink-grey); }
  .person__name { font-size: 31px; font-weight: 700; line-height: 1.1; }
  .person__role { font-size: 21px; font-weight: 400; margin-top: 4px; }
  .contact { position: absolute; left: 39px; top: 580px; list-style: none; color: var(--ink-grey); font-size: 20px; line-height: 26.5px; }
  .contact b { font-weight: 700; }
  .address { position: absolute; left: 39px; top: 713px; color: var(--ink-grey); font-size: 20px; line-height: 27px; font-style: normal; }
  .web { position: absolute; left: 50px; top: 740px; color: var(--ink-light); font-size: 22px; letter-spacing: 2px; }
</style>
</head>
<body>
  <section class="card card--front" aria-label="Business card front">
    <svg class="card__band" viewBox="0 0 454 183" aria-hidden="true">
      <defs>
        <linearGradient id="bandBlueFront" x1="0" x2="1"><stop offset="0" stop-color="var(--brand-blue)"/><stop offset="1" stop-color="var(--brand-blue-deep)"/></linearGradient>
        <linearGradient id="bandDarkFront" x1="0" x2="1"><stop offset="0" stop-color="#2f3032"/><stop offset="1" stop-color="#4a4b4d"/></linearGradient>
      </defs>
      <rect x="230" y="0" width="224" height="183" fill="url(#bandBlueFront)"/>
      <rect x="0" y="0" width="236" height="183" fill="url(#bandDarkFront)"/>
      <circle cx="236" cy="92" r="91" fill="var(--band-dark-edge)"/>
      <circle cx="236" cy="92" r="76" fill="var(--brand-blue)"/>
    </svg>
    <div class="brand-name">Nimbora</div>
    <div class="person">
      <div class="person__name">Your Name</div>
      <div class="person__role">Designation</div>
    </div>
    <ul class="contact">
      <li><b>p</b> : 123-456-7890</li>
      <li><b>c</b> : 123-456-7890</li>
      <li><b>e</b> : name@website.com</li>
      <li><b>w</b> : www.website.com</li>
    </ul>
    <address class="address">City Name, Street Name,<br>State Name, Country Code</address>
    <svg class="card__road" viewBox="0 0 210 380" role="img" aria-label="Blue road arrow decoration">
      <defs><linearGradient id="roadFront" x1="0" y1="0" x2="0" y2="1"><stop offset="0" stop-color="var(--brand-blue)"/><stop offset="1" stop-color="var(--brand-blue-deep)"/></linearGradient></defs>
      <path d="M90 380 C150 300 190 200 210 80 L210 380 Z" fill="url(#roadFront)"/>
    </svg>
  </section>

  <section class="card card--back" aria-label="Business card back">
    <div class="card__top"></div>
    <svg class="card__band" viewBox="0 0 454 183" aria-hidden="true">
      <defs>
        <linearGradient id="bandBlueBack" x1="0" x2="1"><stop offset="0" stop-color="var(--brand-blue)"/><stop offset="1" stop-color="var(--brand-blue-deep)"/></linearGradient>
      </defs>
      <rect x="230" y="0" width="224" height="183" fill="url(#bandBlueBack)"/>
      <rect x="0" y="0" width="236" height="183" fill="var(--card-grey)"/>
      <circle cx="236" cy="92" r="91" fill="var(--band-dark-edge)"/>
      <circle cx="236" cy="92" r="76" fill="var(--brand-blue)"/>
    </svg>
    <div class="brand-name">Nimbora</div>
    <svg class="card__road" viewBox="0 0 210 380" role="img" aria-label="Blue road arrow decoration">
      <defs><linearGradient id="roadBack" x1="0" y1="0" x2="0" y2="1"><stop offset="0" stop-color="var(--brand-blue)"/><stop offset="1" stop-color="var(--brand-blue-deep)"/></linearGradient></defs>
      <path d="M90 380 C150 300 190 200 210 80 L210 380 Z" fill="url(#roadBack)"/>
    </svg>
    <div class="web">www.website.com</div>
  </section>
</body>
</html>
```